Prime Global Casting Agency Needs creative business card design

We manage actors careers and book them liaising and promoting their profiles internationally through Casting Directors, Producers, Directors, Publicists etc. We need clearly visable contact details but with a design that reflects our status and creativity of TV, Feature Film industry. Our logo is attached and needs to relate and our website is www.brisklanestagefolk.com
No flame designs please but please incorporate logo colours.

Target Market(s)

Clients

Industry/Entity Type

Film Production

Contact Information for Business Card

Director Danielle Prowse
Suite F, Building 4, Wrenlow Studios Australia, Kelby Vale, Sydney, NSW 2048

Font styles to use
Sans Serif

Colors
ec1f27

Requirements
Nice to have
• Colours should relate to logo attached and type can relate again to type in the logo design.
Should not have
• No Flames designs and best to be not too obvious with the film designs eiither. Needs to be more creative and modern

```html
<!DOCTYPE html>
<html lang="en">
<head>
<meta charset="utf-8">
<title>Brisklane Stagefolk – Business Card</title>
<link rel="stylesheet" href="https://fonts.googleapis.com/css2?family=Arimo:ital,wght@0,400;0,700;1,700&display=swap">
<style>
  :root {
    --brand-red: #ec1f27;
    --deep-red: #b3161d;
    --dark-red: #8b1116;
    --band-grey: #4a4a4a;
    --silver-light: #f4f4f4;
    --silver-dark: #c9c9c9;
    --logo-light: #eeeeee;
    --ink: #333333;
    --white: #ffffff;
    --page: #ffffff;
  }
  * { margin: 0; padding: 0; box-sizing: border-box; }
  html, body {
    width: 1200px;
    height: 345px;
    overflow: hidden;
    background: var(--page);
    font-family: "Arimo", Arial, sans-serif;
  }
  .canvas {
    position: relative;
    width: 1200px;
    height: 345px;
  }
  .card {
    position: absolute;
    top: 33px;
    width: 487px;
    height: 283px;
    overflow: hidden;
    box-shadow: 2px 3px 6px rgba(0, 0, 0, 0.3);
  }
  .card--front { left: 100px; }
  .card--back { left: 624px; }
  .card__art {
    position: absolute;
    inset: 0;
    width: 100%;
    height: 100%;
  }
  .front-fill {
    position: absolute;
    inset: 0;
    background: linear-gradient(125deg, var(--deep-red) 0%, var(--brand-red) 45%, var(--deep-red) 100%);
  }
  .brand-name {
    position: absolute;
    font-weight: 700;
    color: var(--logo-light);
    white-space: nowrap;
    letter-spacing: 0.5px;
  }
  .card--front .brand-name {
    left: 24px;
    top: 88px;
    font-size: 40px;
  }
  .card--front .website {
    position: absolute;
    left: 24px;
    top: 158px;
    font-size: 12px;
    font-weight: 700;
    color: var(--white);
  }
  .card--back .brand-name {
    left: 32px;
    top: 30px;
    font-size: 27px;
  }
  .contact {
    position: absolute;
    left: 32px;
    top: 134px;
    font-size: 10px;
    line-height: 13px;
    color: var(--white);
    list-style: none;
  }
  .card--back .website {
    position: absolute;
    left: 32px;
    top: 209px;
    font-size: 10px;
    font-weight: 700;
    color: var(--white);
  }
  .person {
    position: absolute;
    right: 14px;
    top: 212px;
    text-align: left;
  }
  .person__name {
    font-size: 22px;
    font-weight: 700;
    font-style: italic;
    color: var(--dark-red);
    line-height: 26px;
    white-space: nowrap;
  }
  .person__role {
    font-size: 12px;
    color: var(--ink);
    line-height: 15px;
  }
</style>
</head>
<body>
<main class="canvas">

  <section class="card card--front" aria-label="Card front">
    <div class="front-fill" role="img" aria-label="Red background of overlapping angular shards"></div>
    <div class="brand-name">Brisklane Stagefolk</div>
    <div class="website">www.brisklanestagefolk.com</div>
  </section>

  <section class="card card--back" aria-label="Card back">
    <svg class="card__art" viewBox="0 0 487 283" preserveAspectRatio="none" aria-hidden="true">
      <defs>
        <linearGradient id="silver" x1="0" y1="0" x2="1" y2="1">
          <stop offset="0" stop-color="var(--silver-dark)"/>
          <stop offset="0.55" stop-color="var(--silver-light)"/>
          <stop offset="1" stop-color="var(--silver-dark)"/>
        </linearGradient>
        <linearGradient id="red-field" x1="0" y1="0" x2="1" y2="1">
          <stop offset="0" stop-color="var(--deep-red)"/>
          <stop offset="0.5" stop-color="var(--brand-red)"/>
          <stop offset="1" stop-color="var(--deep-red)"/>
        </linearGradient>
      </defs>
      <rect class="silver-field" width="487" height="283" fill="url(#silver)"/>
      <path class="curve-band" d="M0 0 H487 V20 C420 125 305 210 180 283 H0 Z" fill="var(--band-grey)"/>
      <path class="red-field" role="img" aria-label="Red background of overlapping angular shards"
            d="M0 0 H370 C330 120 240 210 130 283 H0 Z" fill="url(#red-field)"/>
    </svg>
    <div class="brand-name">Brisklane Stagefolk</div>
    <ul class="contact">
      <li>Suite F, Building 4</li>
      <li>Wrenlow Studios Australia, 12 Harlow Avenue</li>
      <li>Kelby Vale. NSW 2048</li>
      <li>p: +61(0) 4000 55519</li>
      <li>e: talent@brisklanestagefolk.com</li>
    </ul>
    <div class="website">www.brisklanestagefolk.com</div>
    <div class="person">
      <div class="person__name">Danielle Prowse</div>
      <div class="person__role">Director</div>
    </div>
  </section>

</main>
</body>
</html>
```